business card deign

Logo needs the following on it.
1. attached logo
2. Tagline - "If it keeps a drink cold or the party going...we do it!"
3. Name- Dalton Pikes, Founder and CPO
4. Address - 412 E. Carver Avenue, Ste 2207, Tampa, FL. 33917
5. Phone - 555.318.4726

```html
<!DOCTYPE html>
<html lang="en">
<head>
<meta charset="utf-8">
<title>Brisko Business Card</title>
<link rel="stylesheet" href="https://fonts.googleapis.com/css2?family=Oswald:wght@600&family=Open+Sans:wght@400;600;700&display=swap">
<style>
  :root {
    --page-bg: #e6ddd0;
    --card-frost: #d6c9b4;
    --card-edge: #efe6d8;
    --panel-dark: #1b1a19;
    --panel-mid: #2e2d2b;
    --silhouette: #161412;
    --text-light: #d9cfbf;
    --text-muted: #c8bba6;
    --text-dark: #1a1816;
  }
  html, body {
    margin: 0;
    padding: 0;
    width: 1200px;
    height: 1046px;
    overflow: hidden;
    background: var(--page-bg);
  }
  .card {
    position: absolute;
    left: 100px;
    top: 250px;
    width: 1000px;
    height: 545px;
    border-radius: 24px;
    overflow: hidden;
    background: var(--card-frost);
    box-shadow: inset 0 0 0 2px var(--card-edge), 0 12px 30px rgba(60, 45, 25, 0.18);
  }
  .info-panel {
    position: absolute;
    left: 0;
    top: 0;
    width: 600px;
    height: 545px;
    background: linear-gradient(135deg, var(--panel-dark) 0%, var(--panel-mid) 45%, var(--panel-dark) 100%);
  }
  .mascot-area {
    position: absolute;
    left: 600px;
    top: 0;
    width: 285px;
    height: 545px;
    background: var(--silhouette);
  }
  .brand-name {
    position: absolute;
    left: 36px;
    top: 30px;
    margin: 0;
    font-family: "Oswald", "Arial Narrow", sans-serif;
    font-weight: 600;
    font-size: 74px;
    line-height: 1;
    letter-spacing: 34px;
    color: var(--text-light);
  }
  .person {
    position: absolute;
    left: 34px;
    top: 143px;
    margin: 0;
    font-family: "Open Sans", Arial, sans-serif;
  }
  .person-name {
    display: block;
    font-weight: 700;
    font-size: 50px;
    line-height: 1;
    color: var(--text-light);
  }
  .person-title {
    display: block;
    margin-top: 10px;
    font-weight: 600;
    font-size: 24px;
    line-height: 1;
    color: var(--text-muted);
  }
  .contact {
    position: absolute;
    left: 34px;
    top: 268px;
    margin: 0;
    padding: 0;
    list-style: none;
    font-family: "Open Sans", Arial, sans-serif;
    font-size: 25px;
    line-height: 34px;
    color: var(--text-muted);
  }
  .contact-item {
    display: flex;
    align-items: flex-start;
    margin-bottom: 2px;
  }
  .contact-icon {
    width: 20px;
    height: 20px;
    margin: 7px 11px 0 0;
    flex: none;
  }
  .tagline {
    position: absolute;
    left: 910px;
    top: 432px;
    width: 340px;
    margin: 0;
    transform: rotate(-90deg);
    transform-origin: 0 0;
    font-family: "Open Sans", Arial, sans-serif;
    font-weight: 400;
    font-size: 24px;
    line-height: 37px;
    white-space: nowrap;
    color: var(--text-dark);
  }
</style>
</head>
<body>
  <article class="card">
    <div class="info-panel"></div>
    <div class="mascot-area" role="img" aria-label="Standing kangaroo silhouette illustration"></div>

    <h1 class="brand-name">BRISKO</h1>

    <p class="person">
      <span class="person-name">Dalton Pikes</span>
      <span class="person-title">Founder and CPO</span>
    </p>

    <ul class="contact">
      <li class="contact-item">
        <svg class="contact-icon" viewBox="0 0 24 24" aria-hidden="true">
          <path d="M6.6 2.5 L9.5 6.8 L7.6 8.9 C8.7 11.4 10.6 13.3 13.1 14.4 L15.2 12.5 L19.5 15.4 L18 19.4 C11 19.6 4.4 13 4.6 6 Z" fill="none" stroke="var(--text-muted)" stroke-width="2" stroke-linejoin="round"/>
          <path d="M14 3.5 A7 7 0 0 1 20.5 10 M14 7 A3.5 3.5 0 0 1 17 10" fill="none" stroke="var(--text-muted)" stroke-width="1.8" stroke-linecap="round"/>
        </svg>
        <span>555.318.4726</span>
      </li>
      <li class="contact-item">
        <svg class="contact-icon" viewBox="0 0 24 24" aria-hidden="true">
          <path d="M12 2.5 C8.2 2.5 5.5 5.3 5.5 8.8 C5.5 13 12 19.5 12 19.5 C12 19.5 18.5 13 18.5 8.8 C18.5 5.3 15.8 2.5 12 2.5 Z" fill="none" stroke="var(--text-muted)" stroke-width="2"/>
          <circle cx="12" cy="8.8" r="2.4" fill="none" stroke="var(--text-muted)" stroke-width="2"/>
          <path d="M7 22 H17" stroke="var(--text-muted)" stroke-width="2" stroke-linecap="round"/>
        </svg>
        <span>412 E. Carver Avenue,<br>Ste 2207, Tampa, FL. 33917</span>
      </li>
    </ul>

    <p class="tagline">If it keeps a drink cold or<br>the party going...we do it!</p>
  </article>
</body>
</html>
```